Online shopping portal - Business Card Design

Brivamart.com.au is a complete shopping experience. Search, compare & buy items from partnered stores & receive cashbash for your purchases and referrals.
Mission
Our mission is to provide a system for entrepreneurs to create an ongoing income, while providing consumers worldwide with a better way to shop.
A product brokerage and Internet marketing company that specialises in One-to-One Marketing, Quellon Oceania is a subsidiary of Dorvex Holdings Global, Inc.
With more than 3 million Preferred Customers and 180,000 Customer Managers worldwide, Dorvex Holdings has generated over $3 billion USD in accumulated retail sales. The Company employs more than 675 people globally with international operations in Australia, United States, Canada, Taiwan, Hong Kong, Mexico & Singapore
Through revolutionary technology and the one-to-one marketing and social shopping Quellon Oceania are leveraging the Internet with the power of people to create the economy of the future.
By providing online shoppers with the products and services they want and need — backed by the Company’s people power — Quellon Oceania is fast becoming the World Wide Web’s ultimate online shopping destination.
As a result, we are changing the way people shop and changing the economic paradigm where anyone can become financially independent by creating their own economy — Made with Goods. Driven by Folks®.
Description
Welcome to a new kind of comparison shopping site where you get PAID cashback to shop!
Simply create an account to start accumulating cash backs each time you make purchases across hundreds of trusted Partner Stores and thousands of your favorite brands through our convenient PixBasket® for one stop shopping.
All merchant stores are backed by GLIMVEN.NET's 100% satisfaction guarantee.

Updates
Project Deadline Extended
Reason: Hi all,  I am extending the deadline as i'm going to be away for my birthday (and may not have time to check before the current deadline anyway)  I figure that the more time i give you the better.

Industry/Entity Type
Online Shopping
Contact Information for Business Card
Business Name: Brivamart.com.au
website: www.brivamart.com.au
Facebook: www.facebook.com/brivamart.com.au.
Email: info@brivamart.com.au
Phone: Lorn on 0487 52 19 64
Requirements
Nice to have
- Create a Brivamart logo

```html
<!DOCTYPE html>
<html lang="en">
<head>
<meta charset="utf-8">
<title>Brivamart Business Card</title>
<link rel="stylesheet" href="https://fonts.googleapis.com/css2?family=Jura:wght@500;700&family=Michroma&display=swap">
<style>
  :root {
    --stage: #e4e6ea;
    --card-light: #ffffff;
    --card-shade: #dfe1e4;
    --ink: #1f2a36;
    --ink-soft: #2c3744;
    --brand-blue: #1f5fa8;
    --deep-blue: #1c5aa4;
    --cyan: #14cbe8;
  }
  * { box-sizing: border-box; margin: 0; padding: 0; }
  html, body { width: 1200px; height: 899px; overflow: hidden; }
  body {
    background: var(--stage);
    font-family: "Jura", sans-serif;
    color: var(--ink);
    position: relative;
  }
  .card {
    position: absolute;
    width: 665px;
    height: 380px;
    background: radial-gradient(ellipse at 45% 45%, var(--card-light) 0%, #f3f4f5 45%, var(--card-shade) 100%);
    box-shadow: 0 6px 18px rgba(0,0,0,0.18);
    overflow: hidden;
  }
  .card-back { left: 267px; top: 38px; }
  .card-front { left: 267px; top: 480px; }

  .wordmark {
    font-family: "Jura", sans-serif;
    font-weight: 700;
    color: var(--brand-blue);
    letter-spacing: 0.5px;
    white-space: nowrap;
  }
  .card-back .wordmark {
    position: absolute;
    left: 0; right: 0; top: 162px;
    text-align: center;
    font-size: 46px;
  }

  .swoosh { position: absolute; inset: 0; width: 100%; height: 100%; }

  .card-front .wordmark {
    position: absolute;
    left: 40px; top: 138px;
    font-size: 28px;
  }
  .holder {
    position: absolute;
    right: 26px; top: 104px;
    text-align: right;
  }
  .holder-name {
    font-family: "Michroma", sans-serif;
    font-size: 16px;
    letter-spacing: 1.5px;
    color: var(--ink);
  }
  .holder-role {
    font-size: 16px;
    font-weight: 500;
    margin-top: 6px;
    color: var(--ink-soft);
  }
  .contacts {
    position: absolute;
    left: 40px; top: 196px;
    list-style: none;
  }
  .contacts li {
    display: flex;
    align-items: center;
    gap: 10px;
    height: 25px;
    font-size: 15px;
    font-weight: 500;
    letter-spacing: 0.6px;
    color: var(--ink);
  }
  .contacts svg { width: 14px; height: 14px; fill: var(--ink-soft); flex: none; }
  .address {
    position: absolute;
    right: 50px; bottom: 22px;
    text-align: right;
    font-size: 16px;
    font-weight: 500;
    line-height: 1.45;
    letter-spacing: 0.6px;
    color: var(--ink);
  }
</style>
</head>
<body>

<section class="card card-back" aria-label="Card back">
  <div class="wordmark">Brivamart.com.au</div>
</section>

<section class="card card-front" aria-label="Card front">
  <svg class="swoosh" viewBox="0 0 665 380" preserveAspectRatio="none" aria-hidden="true">
    <defs>
      <linearGradient id="bandGrad" x1="0" y1="0" x2="1" y2="0.4">
        <stop offset="0" stop-color="var(--deep-blue)"/>
        <stop offset="0.5" stop-color="var(--cyan)"/>
        <stop offset="1" stop-color="var(--deep-blue)"/>
      </linearGradient>
    </defs>
    <path d="M0,0 H665 V300 C610,150 420,50 0,64 Z" fill="url(#bandGrad)"/>
    <path d="M0,90 C320,50 590,170 665,380 L665,330 C600,170 330,62 0,90 Z" fill="url(#bandGrad)"/>
  </svg>

  <div class="wordmark">Brivamart.com.au</div>

  <div class="holder">
    <div class="holder-name">CALDER VOSS</div>
    <div class="holder-role">Managing Director</div>
  </div>

  <ul class="contacts">
    <li><svg viewBox="0 0 16 16"><path d="M3 1l3 0 1 4-2 1c1 2 3 4 5 5l1-2 4 1 0 3c0 1-1 2-2 2C7 15 1 9 1 3c0-1 1-2 2-2z"/></svg>0487 52 19 64</li>
    <li><svg viewBox="0 0 16 16"><path d="M4 0h8a1 1 0 0 1 1 1v14a1 1 0 0 1-1 1H4a1 1 0 0 1-1-1V1a1 1 0 0 1 1-1zm1 2v10h6V2z"/></svg>0487 52 19 64</li>
    <li><svg viewBox="0 0 16 16"><path d="M4 0h7v4H4zM1 5h14v10H1zm3 2v2h8V7zm0 4v2h2v-2zm4 0v2h2v-2z"/></svg>0487 52 19 64</li>
    <li><svg viewBox="0 0 16 16"><path d="M0 3h16v10H0zm1 1v1l7 4 7-4V4z"/></svg>hello@brivamart.com.au</li>
    <li><svg viewBox="0 0 16 16"><path fill-rule="evenodd" d="M8 0a8 8 0 1 0 0 16A8 8 0 0 0 8 0zm0 1.5a6.5 6.5 0 1 1 0 13a6.5 6.5 0 0 1 0-13zM7.3 1.5h1.4v13H7.3zM1.5 7.3h13v1.4h-13z"/></svg>www.brivamart.com.au</li>
  </ul>

  <div class="address">041.12th floor,Plaza<br>Wrenfield Road QTR</div>
</section>

</body>
</html>
```